Business Card Design Project

Doctor, Pain Management. Need a new business card design with appointment info on the back. New address is 18 Corvell Road, Suite 304, Brisdale, NJ 07391. Right now I believe the rest of the information is staying the same.

```html
<!DOCTYPE html>
<html lang="en">
<head>
<meta charset="utf-8">
<title>Steady Relief Pain Care – Business Card</title>
<link href="https://fonts.googleapis.com/css2?family=Cormorant+Garamond:ital,wght@1,500&family=Tinos:wght@400;700&family=Playfair+Display:wght@900&family=Open+Sans:wght@400&display=swap" rel="stylesheet">
<style>
  :root {
    --ink: #0d0d0d;
    --paper: #ffffff;
    --backdrop: #e4e4e4;
    --accent: #f2ea5a;
    --accent-text: #efe64a;
    --rule: #1a1a1a;
  }
  * { box-sizing: border-box; margin: 0; padding: 0; }
  html, body { width: 1200px; height: 864px; overflow: hidden; background: var(--backdrop); }
  .canvas { position: relative; width: 1200px; height: 864px; }
  .card {
    position: absolute; width: 540px; height: 309px; background: var(--paper);
    overflow: hidden; box-shadow: 0 6px 18px rgba(0,0,0,.18);
    font-family: "Tinos", "Times New Roman", serif; color: var(--ink);
  }
  .card--front { left: 50px; top: 430px; }
  .card--back { left: 610px; top: 125px; }

  /* Front */
  .front-band { position: absolute; left: 0; top: 0; width: 100%; height: 178px; background: var(--ink); }
  .contact-list { position: absolute; left: 18px; top: 16px; list-style: none; color: var(--paper); font-size: 12.5px; line-height: 16px; }
  .contact-list li { display: flex; align-items: center; gap: 8px; white-space: nowrap; }
  .contact-icon { width: 11px; height: 11px; flex: none; }
  .clinic-name {
    position: absolute; left: 190px; top: 92px; font-family: "Cormorant Garamond", Georgia, serif;
    font-style: italic; font-weight: 500; font-size: 33px; color: var(--accent-text); white-space: nowrap;
  }
  .doctor { position: absolute; right: 24px; top: 136px; text-align: right; }
  .doctor-name { font-size: 18px; color: var(--accent-text); line-height: 20px; }
  .doctor-title { font-size: 12.5px; color: var(--paper); line-height: 15px; }
  .photo-row { position: absolute; left: 14px; right: 14px; top: 188px; display: flex; justify-content: space-between; }
  .photo { width: 158px; height: 108px; border: 5px solid var(--ink); }
  .photo--back { background: linear-gradient(160deg, #b7c3e2, #8f9fcb 55%, #d2b49c); }
  .photo--neck { background: linear-gradient(150deg, #f4efe9, #d7a283 55%, #b37a5c); }
  .photo--spine { background: radial-gradient(circle at 50% 55%, #e0632a 0%, #7b3a2c 22%, #566472 55%, #8f9aa6 100%); }

  /* Back */
  .appt-head {
    position: absolute; left: 0; top: 0; width: 100%; height: 42px; background: var(--accent);
    border-bottom: 4px solid var(--rule); display: flex; align-items: center; justify-content: space-between; padding: 0 14px;
  }
  .appt-head .num { font-size: 13px; font-weight: 700; }
  .appt-head .num b { font-style: italic; }
  .appt-title { font-family: "Playfair Display", Georgia, serif; font-weight: 900; font-size: 26px; }
  .field { position: absolute; font-size: 16px; display: flex; align-items: flex-end; gap: 4px; }
  .field .line { flex: 1; border-bottom: 1px solid var(--ink); height: 14px; }
  .field--for { left: 20px; right: 20px; top: 56px; }
  .days { position: absolute; left: 20px; right: 20px; top: 90px; display: flex; justify-content: space-between; font-size: 17px; }
  .days span { display: flex; align-items: center; gap: 3px; }
  .days i { width: 13px; height: 13px; border: 1px solid var(--ink); display: inline-block; }
  .field--date { left: 20px; width: 250px; top: 124px; }
  .field--time { left: 296px; right: 20px; top: 150px; }
  .notice { position: absolute; left: 0; width: 100%; top: 178px; text-align: center; font-size: 15px; font-weight: 700; line-height: 17px; }
  .back-band { position: absolute; left: 0; bottom: 0; width: 100%; height: 66px; background: var(--ink); color: var(--accent-text); font-family: "Open Sans", Arial, sans-serif; }
  .back-band .web { position: absolute; left: 14px; top: 8px; font-size: 13px; }
  .back-band .mail { position: absolute; right: 14px; bottom: 8px; font-size: 14.5px; }
</style>
</head>
<body>
<div class="canvas">

  <section class="card card--back" aria-label="Appointment card, back">
    <header class="appt-head">
      <span class="num"><b>P:</b>(555) 210-4836</span>
      <span class="appt-title">Appoinment</span>
      <span class="num"><b>F:</b>(555) 210.4871</span>
    </header>
    <div class="field field--for">For:<span class="line"></span></div>
    <div class="days">
      <span><i></i>Mon</span><span><i></i>Tue</span><span><i></i>Wed</span><span><i></i>Thu</span>
      <span><i></i>Fri</span><span><i></i>Sat</span><span><i></i>Sun</span>
    </div>
    <div class="field field--date">Date:<span class="line"></span></div>
    <div class="field field--time">Time:<span class="line"></span></div>
    <p class="notice">If you are unable to keep your appoinment,<br>please contact us as soon as posible.</p>
    <footer class="back-band">
      <span class="web">www.steadyreliefpm.com</span>
      <span class="mail">reliefpmc.service@mailbox.com</span>
    </footer>
  </section>

  <section class="card card--front" aria-label="Business card, front">
    <div class="front-band">
      <ul class="contact-list">
        <li><svg class="contact-icon" viewBox="0 0 12 12"><rect width="12" height="12" fill="#f2ea5a"/><path d="M3 2.5h2l.6 2-1 .8a5 5 0 0 0 2.1 2.1l.8-1 2 .6v2A1 1 0 0 1 8.5 10 6.5 6.5 0 0 1 2 3.5a1 1 0 0 1 1-1z" fill="#0d0d0d"/></svg>(555) 210-4836</li>
        <li><svg class="contact-icon" viewBox="0 0 12 12"><rect width="12" height="12" fill="#f2ea5a"/><rect x="2.5" y="4" width="7" height="5" fill="none" stroke="#0d0d0d"/><rect x="4" y="2" width="4" height="2" fill="#0d0d0d"/></svg>(555) 210.4871</li>
        <li><svg class="contact-icon" viewBox="0 0 12 12"><rect width="12" height="12" fill="#f2ea5a"/><rect x="2" y="3.5" width="8" height="5" fill="none" stroke="#0d0d0d"/><path d="M2 3.5l4 3 4-3" fill="none" stroke="#0d0d0d"/></svg>reliefpmc.service@mailbox.com</li>
        <li><svg class="contact-icon" viewBox="0 0 12 12"><rect width="12" height="12" fill="#f2ea5a"/><circle cx="6" cy="6" r="3.5" fill="none" stroke="#0d0d0d"/><path d="M2.5 6h7M6 2.5v7" stroke="#0d0d0d" stroke-width=".8"/></svg>www.steadyreliefpm.com</li>
        <li><svg class="contact-icon" viewBox="0 0 12 12"><rect width="12" height="12" fill="#f2ea5a"/><path d="M6 10.5S3 7 3 5a3 3 0 0 1 6 0c0 2-3 5.5-3 5.5z" fill="#0d0d0d"/><circle cx="6" cy="5" r="1" fill="#f2ea5a"/></svg>18 Corvell Road, Suite 304, Brisdale, NJ 07391</li>
      </ul>
      <h1 class="clinic-name">Steady Relief Pain Care</h1>
      <div class="doctor">
        <p class="doctor-name">Dr. Lianwei Sun</p>
        <p class="doctor-title">M.D., Ph.D.</p>
      </div>
    </div>
    <div class="photo-row">
      <div class="photo photo--back" role="img" aria-label="Photo of a person holding their lower back in pain"></div>
      <div class="photo photo--neck" role="img" aria-label="Photo of a woman's hands rubbing a sore neck and shoulder"></div>
      <div class="photo photo--spine" role="img" aria-label="Illustration of a figure with a highlighted glowing spine showing back pain"></div>
    </div>
  </section>

</div>
</body>
</html>
```